Tollin Waste Website Design

Our new start-up needs a website design. We plan to help businesses find more sustainable ways to manage their waste. Our initial website aims to gather contact data from potential business customers and comprehensive information from waste facilities and waste transporters. We have a logo design (attached) which we would like included in the website design. I have also attached a number of pages that describe what information should appear on each page as well as a web design brief file that describes the look we are after.

```html
<!DOCTYPE html>
<html lang="en">
<head>
<meta charset="utf-8">
<title>Tollin Waste</title>
<link href="https://fonts.googleapis.com/css2?family=Montserrat:wght@400;500;600;700&display=swap" rel="stylesheet">
<style>
:root{
  --green:#5e9b2c;
  --green-bright:#7cb82f;
  --green-dark:#1d3a1d;
  --ink:#333;
  --white:#fff;
  --footer:#1c1c1c;
  --shade:rgba(0,0,0,.72);
}
*{box-sizing:border-box;margin:0;padding:0}
html,body{width:1200px;height:1112px;overflow:hidden}
body{position:relative;background:#f4f4f4;font-family:'Montserrat',sans-serif}
.top-rule{position:absolute;left:0;top:0;width:1200px;height:5px;background:var(--green-dark)}
.site-header{position:absolute;left:0;top:5px;width:1200px;height:99px;background:var(--white)}
.brand{position:absolute;left:86px;top:35px;display:flex;align-items:center;gap:8px;font-weight:700;font-size:26px;color:var(--ink);letter-spacing:1px}
.brand-dot{width:20px;height:20px;border-radius:50%;background:var(--green)}
.main-nav{position:absolute;right:86px;top:44px;display:flex;gap:56px;font-size:12px;font-weight:500;color:var(--green);text-transform:uppercase}
.hero{position:absolute;left:0;top:104px;width:1200px;height:553px;background:linear-gradient(180deg,#5a6d4a 0%,#4a5b44 45%,#6b6a66 75%,#7a7470 100%)}
.hero-line{position:absolute;left:86px;height:55px;padding:0 28px;background:rgba(94,155,44,.85);color:var(--white);font-size:22px;font-weight:500;line-height:55px;white-space:nowrap}
.hero-line.one{top:275px}
.hero-line.two{top:339px}
.services{position:absolute;left:86px;top:698px;display:flex;gap:16px}
.service-card{position:relative;width:332px;height:289px}
.service-photo{position:absolute;inset:0 0 57px 0}
.p1{background:linear-gradient(180deg,#6f8aa3,#8d8c86)}
.p2{background:linear-gradient(180deg,#7d7f7c,#a39a8c)}
.p3{background:linear-gradient(180deg,#8a918f,#b7b7ad)}
.service-band{position:absolute;left:0;bottom:0;width:100%;height:57px;background:var(--green);color:var(--white);font-size:16px;font-weight:600;text-align:center;line-height:57px;text-transform:uppercase}
.service-icon{position:absolute;left:50%;top:190px;width:86px;height:86px;margin-left:-43px;border-radius:50%;background:var(--green);display:flex;justify-content:center;padding-top:14px}
.site-footer{position:absolute;left:0;top:1047px;width:1200px;height:65px;background:var(--footer);color:#bbb;font-family:Arial,sans-serif;font-size:12px;text-align:center;line-height:65px}
.shade{position:absolute;inset:0;background:var(--shade)}
.signup{position:absolute;left:298px;top:190px;width:604px;height:408px;background:var(--white);text-align:center}
.signup-brand{margin-top:60px;display:flex;justify-content:center;align-items:center;gap:10px;font-weight:700;font-size:36px;color:var(--ink);letter-spacing:1px}
.signup-brand .brand-dot{width:28px;height:28px}
.signup-text{margin:34px auto 0;width:480px;font-family:Arial,sans-serif;font-size:12.5px;line-height:26px;color:#222}
.email-field{display:block;margin:28px auto 0;width:471px;height:46px;border:1px solid #999;border-radius:4px;padding:0 13px;font-family:Arial,sans-serif;font-size:13px;color:#222;text-align:left;line-height:44px}
.submit{display:block;margin:19px auto 0;width:126px;height:40px;border:0;border-radius:2px;background:var(--green);color:var(--white);font-family:'Montserrat',sans-serif;font-size:14px;font-weight:600}
.close{position:absolute;left:874px;top:179px;width:46px;height:46px;border-radius:50%;background:#111;border:2px solid var(--white);color:var(--white);font-size:17px;text-align:center;line-height:40px;font-family:Arial,sans-serif}
</style>
</head>
<body>
<div class="top-rule"></div>
<header class="site-header">
  <div class="brand"><span class="brand-dot"></span>TOLLIN WASTE</div>
  <nav class="main-nav"><span>Home</span><span>About Us</span><span>What We Do</span><span>Resources</span><span>Contact Us</span></nav>
</header>
<section class="hero" role="img" aria-label="Photograph of a tree-lined street with a waste collection truck and bins">
  <div class="hero-line one">WELCOME TO TOLLIN WASTE</div>
  <div class="hero-line two">TAKE CONTROL OF YOUR WASTE</div>
</section>
<section class="services">
  <div class="service-card">
    <div class="service-photo p1" role="img" aria-label="Photograph of an industrial site with a chimney"></div>
    <div class="service-icon"><svg width="40" height="40" viewBox="0 0 40 40" fill="none" stroke="#fff" stroke-width="2"><path d="M4 36V20l8 5v-5l8 5v-5l8 5V8h6v28z"/></svg></div>
    <div class="service-band">Waste Producers</div>
  </div>
  <div class="service-card">
    <div class="service-photo p2" role="img" aria-label="Photograph of machinery at a waste facility"></div>
    <div class="service-icon"><svg width="40" height="40" viewBox="0 0 40 40" fill="#fff"><path d="M20 4l7 12h-14zM6 34l7-12 7 12zM34 34H20l7-12z"/></svg></div>
    <div class="service-band">Waste Facilities</div>
  </div>
  <div class="service-card">
    <div class="service-photo p3" role="img" aria-label="Photograph of a waste truck under a steel canopy"></div>
    <div class="service-icon"><svg width="44" height="40" viewBox="0 0 44 40" fill="none" stroke="#fff" stroke-width="2"><path d="M2 12h26v18H2zM28 18h8l6 6v6H28z"/><circle cx="10" cy="32" r="3"/><circle cx="34" cy="32" r="3"/></svg></div>
    <div class="service-band">Waste Transporters</div>
  </div>
</section>
<footer class="site-footer">© Copyright -2018 Tollin Waste Management.All rights reserved.</footer>
<div class="shade"></div>
<div class="signup">
  <div class="signup-brand"><span class="brand-dot"></span>TOLLIN WASTE</div>
  <p class="signup-text">Sed ut perspiciatis unde omnis iste natus error sit voluptatem accusantium doloremque laudantium, totam rem aperiam, eaque ipsa quae ab illo inventore veritatis et quasi arch itecto beatae vitae dicta sunt explicabo.</p>
  <div class="email-field">Enter your email address :</div>
  <button class="submit">SUBMIT</button>
</div>
<div class="close">X</div>
</body>
</html>
```